RTavenor Business Cards & Letterhead

I have a logo but need a design for some new business cards. We are a Design-Build Firm that specializes in the design and construction of commercial projects.
the cards need to be professional. no cartoon stuff.
i would like to have the cards in AI format so I can update the card as needed. Logo is provided.
Our Address is: 4187 Marlowe Ct. Apex, North Carolina 27614

```html
<!DOCTYPE html>
<html lang="en">
<head>
<meta charset="utf-8">
<title>RTavenor Business Card</title>
<link href="https://fonts.googleapis.com/css2?family=Roboto:wght@400;700&display=swap" rel="stylesheet">
<style>
  :root {
    --backdrop: #979797;
    --card-white: #ffffff;
    --brand-blue: #005a8c;
    --accent-blue: #0a6aa8;
    --text-grey: #555555;
    --logo-grey: #5a5a5a;
  }
  html, body {
    margin: 0;
    padding: 0;
    width: 1200px;
    height: 1000px;
    overflow: hidden;
    background: var(--backdrop);
    font-family: "Roboto", sans-serif;
  }
  .canvas {
    position: relative;
    width: 1200px;
    height: 1000px;
  }
  .card {
    position: absolute;
    left: 301px;
    width: 604px;
    height: 366px;
    border-bottom-right-radius: 205px;
    overflow: hidden;
  }
  .card-front { top: 116px; background: var(--card-white); }
  .card-back { top: 537px; background: var(--brand-blue); }

  .wordmark-vertical {
    position: absolute;
    left: 134px;
    top: 196px;
    transform: translate(-50%, -50%) rotate(-90deg);
    font-weight: 700;
    font-size: 48px;
    letter-spacing: 1px;
    color: var(--logo-grey);
    white-space: nowrap;
    line-height: 1;
  }

  .contact {
    position: absolute;
    left: 223px;
    top: 50px;
    color: var(--text-grey);
    font-size: 22px;
    line-height: 28px;
  }
  .contact p { margin: 0; white-space: nowrap; }
  .contact-name { font-weight: 700; font-size: 22px; }
  .contact-role { margin-bottom: 10px !important; }
  .contact-rule {
    width: 74px;
    height: 3px;
    background: var(--accent-blue);
    margin: 0 0 22px 2px;
  }
  .contact-address { margin-bottom: 26px !important; }
  .contact-reach { margin-bottom: 26px !important; }
  .contact-web { font-weight: 700; color: var(--brand-blue); }

  .wordmark-large {
    position: absolute;
    left: 60px;
    top: 150px;
    font-weight: 700;
    font-size: 64px;
    color: var(--card-white);
    letter-spacing: 1px;
    line-height: 1;
    white-space: nowrap;
  }
</style>
</head>
<body>
<div class="canvas">
  <section class="card card-front">
    <div class="wordmark-vertical">RTAVENOR</div>
    <div class="contact">
      <p class="contact-name">REID TAVENOR</p>
      <p class="contact-role">President</p>
      <div class="contact-rule"></div>
      <p>4187 Marlowe Ct. Apex</p>
      <p class="contact-address">North Carolina 27614</p>
      <p>reid@rtavenor.com</p>
      <p class="contact-reach">919-555-0148</p>
      <p class="contact-web">rtavenor.com</p>
    </div>
  </section>

  <section class="card card-back">
    <div class="wordmark-large">RTavenor</div>
  </section>
</div>
</body>
</html>
```